Foodcard Package Design for 10ml Food Enhancer

I have developed a product with a friend that we will be selling later this year, it is a liquid that comes in a small 10ml or 20ml bottle for sale in shops (a flavour enhancer).

A small cardboard sized backer of approximate size "A5" is the best packaging for this product.

i have attached an example of what I am looking for - the front will hold the bottle inside a small plastic case, and the back will be how to use the product / instructions.

What I am looking for is:
Strong graphic design skills to capture customers attention
Good layout of "how to use" instructions so it is clear for customer to understand
Similar "feel" to attached document as guide only

(Note: I will add the words myself, the graphics is all I need. When you design the front & back you will add Lorem ipsom text to display position of text only).

Target Market(s)

Retail & Restaurant industry

Industry/Entity Type

Retail

Font styles to use
Serif

Requirements
Must have
• Captures customers attention, high impact, sophisticated
Nice to have
• Colour, cutting edge look
Should not have
• Not cheap looking

```html
<!DOCTYPE html>
<html lang="en">
<head>
<meta charset="utf-8">
<title>The Hidden Kitchen Secret – Backer Card</title>
<link rel="stylesheet" href="https://fonts.googleapis.com/css2?family=Cinzel+Decorative:wght@400;700&family=Questrial&display=swap">
<style>
  :root {
    --page: #ffffff;
    --ink: #111111;
    --rule: #222222;
    --card-edge: #1a1a1a;
    --wood-light: #d9ad7c;
    --wood-mid: #c48d5a;
    --wood-dark: #a86f40;
    --blister: rgba(255, 255, 255, 0.38);
    --blister-edge: rgba(120, 120, 120, 0.55);
  }
  * { box-sizing: border-box; margin: 0; padding: 0; }
  html, body { width: 1200px; height: 895px; overflow: hidden; background: var(--page); }
  .canvas { position: relative; width: 1200px; height: 895px; }

  .card {
    position: absolute; top: 44px; width: 451px; height: 798px;
    border: 1.5px solid var(--card-edge); border-radius: 26px; overflow: hidden;
  }
  .card--front { left: 116px; }
  .card--back { left: 627px; background: var(--page); }

  .front-photo {
    position: absolute; inset: 0;
    background:
      radial-gradient(ellipse 30% 45% at 5% 15%, rgba(95,155,58,0.9), transparent 70%),
      radial-gradient(ellipse 35% 30% at 90% 95%, rgba(200,48,42,0.85), transparent 70%),
      radial-gradient(ellipse 30% 25% at 10% 90%, rgba(240,232,220,0.9), transparent 70%),
      radial-gradient(ellipse 25% 20% at 85% 10%, rgba(240,210,140,0.9), transparent 70%),
      linear-gradient(90deg, var(--wood-mid), var(--wood-light) 45%, var(--wood-mid) 75%, var(--wood-dark));
  }

  .hang-tab { position: absolute; left: 0; top: 0; }

  .title {
    position: absolute; top: 80px; left: 0; width: 100%; text-align: center;
    font-family: "Cinzel Decorative", "Cinzel", serif; font-weight: 400;
    font-size: 41px; line-height: 37px; color: var(--ink); letter-spacing: 0.5px;
  }
  .card--front .title { text-shadow: 0 0 10px #fff, 0 0 18px #fff, 0 0 4px #fff; }
  .card--back .title { text-shadow: 2px 2px 3px rgba(0,0,0,0.25); }

  .tagline {
    position: absolute; top: 161px; left: 0; width: 100%; text-align: center;
    font-family: "Questrial", sans-serif; font-size: 16px; line-height: 21px; color: var(--ink);
    text-shadow: 0 0 6px #fff, 0 0 10px #fff;
  }

  .blister {
    position: absolute; left: 174px; top: 217px; width: 100px; height: 552px;
    border-radius: 22px; background: var(--blister); border: 1px solid var(--blister-edge);
  }

  .title-rule { position: absolute; left: 51px; top: 167px; width: 349px; border-top: 1.5px solid var(--rule); }
  .section-rule { position: absolute; left: 41px; width: 369px; border-top: 1.5px solid var(--rule); }

  .usage {
    position: absolute; left: 20px; width: 411px; text-align: center;
    font-family: "Questrial", sans-serif; font-size: 17.5px; line-height: 21px; color: var(--ink);
  }
  .usage h2 { font-weight: 400; font-size: 17.5px; line-height: 21px; }
  .usage p + p { margin-top: 21px; }
</style>
</head>
<body>
<div class="canvas">

  <section class="card card--front">
    <div class="front-photo" role="img" aria-label="Photograph of a wooden kitchen table framed by cucumbers, pasta, peppercorns, chilli, spinach, mushrooms, garlic and cherry tomatoes"></div>
    <svg class="hang-tab" width="451" height="80" viewBox="0 0 451 80" aria-hidden="true">
      <circle cx="221" cy="40" r="10" fill="#ffffff"/>
      <rect x="178" y="39" width="84" height="18" rx="9" fill="#ffffff"/>
    </svg>
    <h1 class="title">The Hidden<br>Kitchen Secret</h1>
    <p class="tagline">ADD TO BOILING WATER<br>FOR FARMHOUSE STYLE VEGETABLES</p>
    <div class="blister" aria-label="Clear blister holding the bottle"></div>
  </section>

  <section class="card card--back">
    <svg class="hang-tab" width="451" height="80" viewBox="0 0 451 80" aria-hidden="true">
      <path d="M186 41 h26 a13 12 0 0 1 26 0 h26 a8 8 0 0 1 0 16 h-78 a8 8 0 0 1 0 -16 z" fill="none" stroke="#111" stroke-width="1.5"/>
    </svg>
    <h1 class="title">The Hidden<br>Kitchen Secret</h1>
    <div class="title-rule"></div>

    <div class="usage" style="top:186px">
      <h2>MASHED POTATOES</h2>
      <p>Add wooded earth and charm to mashed<br>potatoes.<br>Can be used in place of cream &amp; butter.</p>
      <p>Add 2 drops to your bowl of mashed potatoes<br>for an earth charm flavour.</p>
    </div>
    <div class="section-rule" style="top:344px"></div>

    <div class="usage" style="top:355px">
      <h2>RICE</h2>
      <p>Or apply to boiled rice for a smoky plume”<br>Once rice is cooked stir in 2 drops and<br>experience the difference</p>
    </div>
    <div class="section-rule" style="top:448px"></div>

    <div class="usage" style="top:459px">
      <h2>SAUCES</h2>
      <p>Do you make your own sauces?<br>Stir in 2 drops to your sauces for an extra level of<br>depth.</p>
    </div>
    <div class="section-rule" style="top:556px"></div>

    <div class="usage" style="top:564px">
      <h2>STEWS CASSEROLES</h2>
      <p>Add 2 drops to your bowl of mashed potatoes<br>for a smokey charm</p>
    </div>
    <div class="section-rule" style="top:641px"></div>

    <div class="usage" style="top:648px">
      <h2>PERFECT WHISKY</h2>
      <p>Mix with water and freeze into ice cube trays.<br>Add cubes to torn ordinary whisky into a<br>premium aged whisky</p>
    </div>
  </section>

</div>
</body>
</html>
```